Website for steady harbor detailing.

Need a homepage, pages for: car and truck detailing, boat detailing, airplane detailing, about us, contact us. I have the domain name through nimbushelm so I will need the design uploaded on my domain. Also hoping to link other domains to this page.I would like to see the logo more pronounced. I would like to see a large phone number link to call my business. The layout looks nice but the pics need to depict car washing and waxing not car mechanics. i would like the colors of the webpage to incorporate the colors found in the logo in some way. I would like links to social media pages
Updates

Target Market(s)

Local customers in Vero Beach, Florida.

Number of Pages Required

5+ page

Colors

Requirements
Must have
• Easy to navigate, attractive pages with pictures and logo, professional looking. must have my phone number and logo very prevalent and links to call or go to home page. I would like links to my social media accounts on the home page.
Nice to have
• Easy to navigate, attractive pages with pictures and logo, professional looking.

```html
<!DOCTYPE html>
<html lang="en">
<head>
<meta charset="utf-8">
<title>Steady Harbor Detailing</title>
<link href="https://fonts.googleapis.com/css2?family=Nunito:wght@700;800&family=Lato:wght@400;700&display=swap" rel="stylesheet">
<style>
:root{
  --red:#e8202a;
  --navy:#2e3192;
  --sky:#1fa9e1;
  --sky-deep:#1b95cf;
  --purple:#3a3d8c;
  --grey-bg:#f4f4f4;
  --text:#555;
  --white:#fff;
}
*{box-sizing:border-box;margin:0;padding:0}
html,body{width:1200px;height:3237px;overflow:hidden}
body{position:relative;font-family:"Lato",sans-serif;color:var(--text);background:var(--white)}
.abs{position:absolute}
h1,h2,h3,.brand{font-family:"Nunito",sans-serif}
.btn{position:absolute;background:var(--red);color:var(--white);font-size:22px;display:flex;align-items:center;justify-content:center;letter-spacing:.5px;clip-path:polygon(0 0,100% 0,88% 100%,0 100%);padding-right:16px}
.ph{position:absolute}

/* top bar */
.topbar{left:0;top:0;width:1200px;height:43px;background:var(--red);color:var(--white);font-size:17px}
.topbar .call{position:absolute;right:35px;top:10px;display:flex;align-items:center;gap:12px}
.navbar{left:0;top:43px;width:1200px;height:82px;background:var(--navy)}
.navbar ul{position:absolute;left:516px;top:30px;display:flex;gap:0;list-style:none;color:var(--white);font-size:17px}
.navbar li{margin-right:50px}
.search{position:absolute;left:1080px;top:17px;width:42px;height:42px;border:2px solid var(--white);border-radius:50%}
.logo-box{left:65px;top:0;width:330px;height:125px;background:var(--white);clip-path:polygon(0 0,260px 0,330px 125px,0 125px);border-left:6px solid var(--sky)}
.logo-edge{left:320px;top:0;width:75px;height:125px;background:var(--sky);clip-path:polygon(0 0,10px 0,75px 125px,65px 125px)}
.brand{position:absolute;display:flex;align-items:center;gap:10px;color:var(--navy);font-weight:800}
.logo-box .brand{left:22px;top:30px;font-size:24px;line-height:1.1;width:230px}
.dot{width:22px;height:22px;border-radius:50%;background:var(--red);flex:none}

/* hero */
.hero-photo{left:0;top:125px;width:680px;height:572px;background:linear-gradient(120deg,#d9dde2 0%,#b9bec4 45%,#8a8f8f 100%)}
.hero-panel{left:680px;top:125px;width:520px;height:572px;background:linear-gradient(160deg,#3cc0ee,#1fa4dc)}
.hero-panel h1{position:absolute;left:28px;top:122px;font-size:42px;line-height:50px;color:var(--white);font-weight:800}
.hero-panel p{position:absolute;left:28px;top:235px;width:440px;font-size:16px;line-height:26px;color:var(--white)}
.hero-dots{left:618px;top:663px;width:92px;height:34px;background:#2f5b7a;display:flex;gap:10px;justify-content:center;align-items:center}
.hero-dots i{width:10px;height:10px;border:2px solid var(--white);border-radius:50%}
.hero-dots i.on{background:var(--white)}

/* section headings */
.sec-title{position:absolute;left:0;width:1200px;text-align:center;font-size:38px;font-weight:800;color:var(--navy)}
.sec-title span{color:var(--sky)}
.sec-rule{position:absolute;left:480px;width:240px;height:2px;background:#d6d6d6}
.sec-rule::after{content:"";position:absolute;left:114px;top:-4px;width:10px;height:10px;border-radius:50%;background:#c8c8c8}

.about p{position:absolute;left:230px;top:852px;width:740px;text-align:center;font-size:14px;line-height:25px}

/* services */
.services{left:0;top:1137px;width:1200px;height:708px;background:var(--grey-bg)}
.svc-img{height:218px;top:1293px;width:332px;background:linear-gradient(135deg,#9aa6b0,#55606b)}
.svc h3{position:absolute;top:1540px;font-size:22px;font-weight:800;color:var(--navy)}
.svc p{position:absolute;top:1578px;width:330px;font-size:14px;line-height:25px}

/* quote + testimonials */
.testi-bg{left:0;top:1845px;width:1200px;height:520px;background:linear-gradient(90deg,#3a3d8c,#4a4fa0 60%,#3a3d8c)}
.quote{left:97px;top:1824px;width:417px;height:541px;background:var(--sky);clip-path:polygon(20px 0,100% 0,100% 100%,0 100%,0 20px)}
.quote h2{position:absolute;left:0;width:417px;top:44px;text-align:center;font-size:29px;color:var(--white);font-weight:800}
.quote .line{position:absolute;left:120px;top:92px;width:177px;height:2px;background:var(--white)}
.field{position:absolute;left:43px;width:330px;height:42px;background:var(--white);border-radius:4px;font-size:14px;color:#666;padding:12px 10px}
.field.msg{height:72px}
.testi h2{position:absolute;left:514px;width:686px;top:1900px;text-align:center;font-size:35px;color:var(--white);font-weight:800}
.avatar{left:815px;top:1982px;width:115px;height:110px;border:6px solid var(--sky);background:linear-gradient(#e8e8ec,#c5c7d2)}
.qmark{left:905px;top:2063px;width:44px;height:44px;background:var(--sky);color:var(--white);font-family:"Nunito",sans-serif;font-size:42px;font-weight:800;text-align:center;line-height:56px}
.testi p{position:absolute;left:565px;width:590px;top:2138px;text-align:center;color:var(--white);font-size:15px;line-height:26px}
.testi .who{position:absolute;left:514px;width:686px;top:2222px;text-align:center;color:var(--white);font-size:16px;font-weight:700}
.sq-dots{left:1045px;top:2287px;display:flex;gap:4px}
.sq-dots i{width:14px;height:14px;border:1.5px solid var(--white)}
.sq-dots i.on{background:var(--sky);border-color:var(--sky)}
.arrow{position:absolute;top:2055px;color:#cdd0ea;font-size:38px;font-family:"Lato",sans-serif}

/* blog */
.blog-img{top:2520px;width:250px;height:167px;background:linear-gradient(135deg,#8896a2,#3f4a55)}
.post h3{position:absolute;top:2706px;width:250px;font-size:16px;line-height:24px;color:var(--sky-deep);font-weight:800}
.post a{position:absolute;top:2766px;font-size:14px;color:var(--navy);text-decoration:none;display:flex;align-items:center;gap:8px}
.post a i{width:18px;height:18px;border:1.5px solid var(--sky);border-radius:50%;font-style:normal;font-size:11px;color:var(--sky);text-align:center;line-height:15px}

/* footer */
.footer{left:0;top:2845px;width:1200px;height:327px;background:linear-gradient(160deg,#2ab1e6,#1c9ed8)}
.foot-nav{left:78px;top:2909px;display:flex;align-items:center;color:var(--white);font-size:15px}
.foot-nav .home{background:var(--red);width:70px;height:48px;display:flex;align-items:center;justify-content:center}
.foot-nav span{padding:0 16px;border-right:1px solid var(--white);line-height:14px}
.foot-nav span:last-child{border:none}
.foot-logo{left:902px;top:2874px;width:220px;height:93px;background:var(--white)}
.foot-logo .brand{left:18px;top:22px;font-size:20px;line-height:1.1;width:190px}
.foot-rule{left:0;top:3000px;width:1200px;height:1px;background:rgba(255,255,255,.35)}
.contact{position:absolute;top:3056px;display:flex;align-items:center;gap:18px;color:var(--white);font-size:15px;line-height:21px}
.cicon{width:52px;height:52px;background:var(--red);clip-path:polygon(0 0,100% 0,82% 100%,0 100%);display:flex;align-items:center;justify-content:center;padding-right:8px;flex:none}
.contact b{font-family:"Nunito",sans-serif;font-size:19px;display:block}
.bottom{left:0;top:3172px;width:1200px;height:65px;background:var(--red);color:var(--white);font-size:14px}
.bottom p{position:absolute;left:78px;top:24px}
.social{position:absolute;top:12px;width:40px;height:40px;background:var(--navy)}
</style>
</head>
<body>

<header>
  <div class="abs topbar">
    <div class="call">Call Us Now
      <svg width="22" height="22" viewBox="0 0 24 24"><path fill="#fff" d="M6.6 10.8a15 15 0 0 0 6.6 6.6l2.2-2.2c.3-.3.7-.4 1-.2 1.1.4 2.3.6 3.6.6.6 0 1 .4 1 1V20c0 .6-.4 1-1 1A17 17 0 0 1 3 4c0-.6.4-1 1-1h3.5c.6 0 1 .4 1 1 0 1.3.2 2.5.6 3.6.1.3 0 .7-.2 1z"/></svg>
      555 - 014 - 2290</div>
  </div>
  <nav class="abs navbar">
    <ul><li>Home</li><li>About Us</li><li>Our Services</li><li>Blog</li><li>Contact Us</li></ul>
    <div class="search"><svg width="38" height="38" viewBox="0 0 38 38"><circle cx="17" cy="17" r="7" fill="none" stroke="#fff" stroke-width="2"/><path d="M22 22l6 6" stroke="#fff" stroke-width="2"/></svg></div>
  </nav>
  <div class="abs logo-box"><div class="brand"><span class="dot"></span>Steady Harbor Detailing</div></div>
  <div class="abs logo-edge"></div>
</header>

<section class="hero">
  <div class="ph hero-photo" role="img" aria-label="Worker in protective suit polishing a boat hull in a boatyard"></div>
  <div class="abs hero-panel">
    <h1>ALL STEADY HARBOR<br>DETAILING</h1>
    <p>Lorem Ipsum is simply dummy text of the printing and typesetting industry. Lorem Ipsum has been the Print industry's standard dummy text ever since the 1500s.</p>
  </div>
  <div class="btn" style="left:708px;top:460px;width:194px;height:62px">CONTACT US</div>
  <div class="abs hero-dots"><i></i><i class="on"></i><i></i></div>
</section>

<section class="about">
  <h2 class="sec-title" style="top:762px">About <span>Steady Harbor Detailing</span></h2>
  <div class="sec-rule" style="top:821px"></div>
  <p>Lorem Ipsum is simply dummy text of the printing and typesetting industry. Lorem Ipsum has been the industry's standard dummy text ever since the 1500s, when an unknown printer took a galley of type and scrambled it to make a type specimen book. It has survived not only five centuries, but also the leap into electronic typesetting, text remaining essentially unchanged. It was popularised in the 1960s with the release of Letraset sheets containing Lorem Ipsum passages.</p>
  <div class="btn" style="left:503px;top:1010px;width:194px;height:62px">READ MORE</div>
</section>

<section>
  <div class="abs services"></div>
  <h2 class="sec-title" style="top:1178px">Our <span>Services</span></h2>
  <div class="sec-rule" style="top:1237px"></div>
  <div class="svc">
    <div class="ph svc-img" style="left:78px" role="img" aria-label="Man washing a car windshield with a sponge"></div>
    <h3 style="left:78px">Car and Truck Detailing</h3>
    <p style="left:78px">Lorem Ipsum is simply dummy text of the printing and typesetting industry. Lorem Ipsum has been the industry's standard dummy 1500s.</p>
    <div class="btn" style="left:78px;top:1677px;width:182px;height:54px">READ MORE</div>
  </div>
  <div class="svc">
    <div class="ph svc-img" style="left:434px" role="img" aria-label="Man cleaning a boat deck at a marina"></div>
    <h3 style="left:434px">Boat Detailing</h3>
    <p style="left:434px">Lorem Ipsum is simply dummy text of the printing and typesetting industry. Lorem Ipsum has been the industry's standard dummy 1500s.</p>
    <div class="btn" style="left:434px;top:1677px;width:182px;height:54px">READ MORE</div>
  </div>
  <div class="svc">
    <div class="ph svc-img" style="left:790px" role="img" aria-label="Worker polishing the side of an aircraft"></div>
    <h3 style="left:790px">Airplane Detailing</h3>
    <p style="left:790px">Lorem Ipsum is simply dummy text of the printing and typesetting industry. Lorem Ipsum has been the industry's standard dummy 1500s.</p>
    <div class="btn" style="left:790px;top:1677px;width:182px;height:54px">READ MORE</div>
  </div>
</section>

<section class="testi">
  <div class="ph testi-bg" role="img" aria-label="Car being washed with foam, tinted in deep blue"></div>
  <span class="arrow" style="left:74px">&#8249;</span>
  <span class="arrow" style="left:1108px">&#8250;</span>
  <div class="abs quote">
    <h2>Request Quote</h2>
    <div class="line"></div>
    <div class="field" style="top:121px">Full Name:</div>
    <div class="field" style="top:173px">Mobile Number:</div>
    <div class="field" style="top:225px">Email Address:</div>
    <div class="field" style="top:277px">Best time of services:
      <svg style="position:absolute;right:10px;top:14px" width="16" height="10" viewBox="0 0 16 10"><path d="M1 1l7 7 7-7" fill="none" stroke="#666" stroke-width="2"/></svg></div>
    <div class="field msg" style="top:329px">Message</div>
    <div class="btn" style="left:117px;top:437px;width:182px;height:52px">SUBMIT INFO</div>
  </div>
  <h2>What Our Client Say</h2>
  <div class="ph avatar" role="img" aria-label="Client portrait"></div>
  <div class="abs qmark">&#8220;</div>
  <p>Lorem Ipsum is simply dummy text of the printing and typesetting industry. Lorem Ipsum has been the industry's standard dummy text ever since the 1500s, when an unknown printer took a galley of type and scrambled.</p>
  <div class="who">- DARA MILLS</div>
  <div class="abs sq-dots"><i></i><i class="on"></i><i></i><i></i></div>
</section>

<section class="blog">
  <h2 class="sec-title" style="top:2420px">Latest <span>Blog</span></h2>
  <div class="sec-rule" style="top:2479px"></div>
  <div class="post">
    <div class="ph blog-img" style="left:78px" role="img" aria-label="Crew hand washing a dark car"></div>
    <h3 style="left:78px">Lorem Ipsum simply dummy typesetting industry.</h3>
    <a style="left:78px">READ MORE <i>&#8250;</i></a>
  </div>
  <div class="post">
    <div class="ph blog-img" style="left:343px" role="img" aria-label="Man cleaning a yacht on the water"></div>
    <h3 style="left:343px">Lorem Ipsum simply dummy typesetting industry.</h3>
    <a style="left:343px">READ MORE <i>&#8250;</i></a>
  </div>
  <div class="post">
    <div class="ph blog-img" style="left:608px" role="img" aria-label="Machine polisher buffing a car panel"></div>
    <h3 style="left:608px">Lorem Ipsum simply dummy typesetting industry.</h3>
    <a style="left:608px">READ MORE <i>&#8250;</i></a>
  </div>
  <div class="post">
    <div class="ph blog-img" style="left:874px" role="img" aria-label="Foam covered car being washed"></div>
    <h3 style="left:874px">Lorem Ipsum simply dummy typesetting industry.</h3>
    <a style="left:874px">READ MORE <i>&#8250;</i></a>
  </div>
</section>

<footer>
  <div class="ph footer" role="img" aria-label="Marina with boats, tinted sky blue"></div>
  <div class="abs foot-nav"><div class="home">Home</div><span style="margin-left:20px">About</span><span>Services</span><span>Blog</span><span>Contact</span></div>
  <div class="abs foot-logo"><div class="brand"><span class="dot"></span>Steady Harbor Detailing</div></div>
  <div class="abs foot-rule"></div>

  <div class="contact" style="left:78px">
    <div class="cicon"><svg width="22" height="26" viewBox="0 0 24 28"><path fill="#fff" d="M12 0a9 9 0 0 0-9 9c0 7 9 19 9 19s9-12 9-19a9 9 0 0 0-9-9zm0 13a4 4 0 1 1 0-8 4 4 0 0 1 0 8z"/></svg></div>
    <div><b>Harbor Office</b>123 Street, Landmark,<br>Country 123456</div>
  </div>
  <div class="contact" style="left:354px">
    <div class="cicon"><svg width="22" height="22" viewBox="0 0 24 24"><path fill="#fff" d="M6.6 10.8a15 15 0 0 0 6.6 6.6l2.2-2.2c.3-.3.7-.4 1-.2 1.1.4 2.3.6 3.6.6.6 0 1 .4 1 1V20c0 .6-.4 1-1 1A17 17 0 0 1 3 4c0-.6.4-1 1-1h3.5c.6 0 1 .4 1 1 0 1.3.2 2.5.6 3.6.1.3 0 .7-.2 1z"/></svg></div>
    <div>555 - 014 - 2290</div>
  </div>
  <div class="contact" style="left:582px">
    <div class="cicon"><svg width="24" height="18" viewBox="0 0 24 18"><rect x="1" y="1" width="22" height="16" fill="none" stroke="#fff" stroke-width="2"/><path d="M1 1l11 9 11-9" fill="none" stroke="#fff" stroke-width="2"/></svg></div>
    <div style="font-size:14px">info@steadyharbordetailing.com</div>
  </div>
  <div class="contact" style="left:884px">
    <div class="cicon"><svg width="24" height="24" viewBox="0 0 24 24" fill="none" stroke="#fff" stroke-width="1.8"><circle cx="12" cy="12" r="10"/><ellipse cx="12" cy="12" rx="4.5" ry="10"/><path d="M2 12h20M4 6.5h16M4 17.5h16"/></svg></div>
    <div style="font-size:14px">www.steadyharbor<br>detailing.com</div>
  </div>

  <div class="abs bottom">
    <p>&copy; STEADY HARBOR DETAILING - 2018. All Rights Reserved.</p>
    <div class="social" style="left:972px" aria-label="Social link"></div>
    <div class="social" style="left:1024px" aria-label="Social link"></div>
    <div class="social" style="left:1076px" aria-label="Social link"></div>
  </div>
</footer>

</body>
</html>
```